Fire Risk Assessment App needs a sleek UI design

I need a sleek, modern but professional design for my 5 page Fire Risk Assessment App. Include gradient background, fire themed colours including reds, yellows, light orange and a touch of black. Design must ooze simplicity and professionalism. This is for the UK market. See attached images and word doc for more information.

Target Market(s)

General public and business owners

Industry/Entity Type

Technology / Fire Safety

Colors
00AB8E
00BBA5
67D7C9
C6EFE9
E9F9F6
59FF00
82FF00
B8FF75
E3FFCB
F4FFEA
FFC000
F8CF3A
FAE287
FDF2CF
FEFAEE
F0912C
F2A743
F7CA91
FBE8D2
FDF5EE
EE7325
F08F49
F5BC92
FAE3D3
FDF4ED
EB3D1F
EC4F4E
F09395
F8D3D4
FCEDEE

```html
<!DOCTYPE html>
<html lang="en">
<head>
<meta charset="utf-8">
<title>Fire Risk Assessment App – Screens</title>
<link rel="stylesheet" href="https://fonts.googleapis.com/css2?family=DM+Sans:wght@400;500;700&display=swap">
<style>
:root{
  --stage:#F0A044;
  --screen-top:#FFFFFF;
  --screen-bottom:#FBEBD9;
  --ink:#2E2E2E;
  --ink-soft:#555555;
  --muted:#9A9A9A;
  --gold:#F8CF3A;
  --gold-deep:#F2B53A;
  --maroon:#A30008;
  --red:#EB1C24;
  --red-bright:#EB3D1F;
  --green:#1EC43C;
  --orange:#FFA400;
  --orange-icon:#F0912C;
  --ring:#2BC93B;
  --white:#FFFFFF;
  --nav-icon:#6E6E6E;
}
*{box-sizing:border-box;margin:0;padding:0}
html,body{width:1200px;height:551px;overflow:hidden}
body{background:var(--stage);font-family:'DM Sans',sans-serif;color:var(--ink);position:relative}
.screen{position:absolute;top:70px;width:199px;height:432px;border-radius:26px;overflow:hidden;
  background:linear-gradient(180deg,var(--screen-top) 0%,#FDF5EE 55%,var(--screen-bottom) 100%);
  box-shadow:0 10px 24px rgba(120,60,0,.25)}
.screen--welcome{left:86px}
.screen--dashboard{left:362px}
.screen--support{left:643px}
.screen--question{left:924px}
.abs{position:absolute}
.center-text{left:0;right:0;text-align:center}
.t{line-height:1;white-space:nowrap}

/* welcome */
.welcome__headline{top:30px;font-size:10.5px;line-height:1.3;color:var(--ink-soft)}
.welcome__preview{left:28px;top:64px;width:132px;height:122px;border-radius:4px;
  background:linear-gradient(160deg,#FFFFFF 0%,#FBE8D2 70%,#F7CA91 100%)}
.welcome__tagline{top:198px;font-size:10.5px;line-height:1.3;color:var(--ink-soft)}
.btn{position:absolute;display:flex;align-items:center;justify-content:center;gap:8px;font-weight:500;border-radius:4px}
.btn--create{left:20px;top:252px;width:158px;height:25px;font-size:9.5px;color:var(--ink);
  background:linear-gradient(180deg,var(--gold),var(--gold-deep));box-shadow:0 3px 5px rgba(0,0,0,.15)}
.btn--login{left:20px;top:318px;width:158px;height:25px;font-size:9.5px;color:var(--white);
  background:var(--maroon);box-shadow:0 3px 5px rgba(0,0,0,.2)}
.welcome__note{top:294px;font-size:10px;color:var(--ink-soft)}
.welcome__finger{left:85px;top:359px;width:29px;height:33px;border-radius:5px;background:var(--white);
  box-shadow:0 1px 4px rgba(0,0,0,.15);display:flex;align-items:center;justify-content:center}
.welcome__footer{top:405px;font-size:8px;color:var(--ink-soft)}

/* headers */
.screen__title{top:32px;display:flex;align-items:center;justify-content:center;gap:5px;font-size:10.5px;letter-spacing:.2px}

/* dashboard */
.dash__start{top:60px;font-size:7.5px;font-weight:500}
.dash__type{top:163px;font-size:7.5px;width:60px;text-align:center}
.status{position:absolute;left:20px;width:96px;height:21px;border-radius:3px;color:var(--white);font-size:9.5px;font-weight:500;
  display:flex;align-items:center;justify-content:space-between;padding:0 8px 0 11px}
.status--complete{top:187px;background:var(--green)}
.status--progress{top:240px;background:var(--orange)}
.status--purchases{top:313px;background:var(--red)}
.site{position:absolute;left:20px;display:flex;align-items:center;gap:7px;font-size:9.5px;line-height:1}
.site--small{font-size:8.7px}
.site__mark{width:10px;height:10px;border-radius:2px;background:linear-gradient(180deg,#C9D6EA,#8EA2C3)}
.site__mark--home{background:linear-gradient(180deg,#EC4F4E,#F7CA91)}

/* nav */
.nav{position:absolute;left:0;right:0;bottom:0;height:30px;background:var(--white);border-radius:14px 14px 0 0;
  display:flex;justify-content:space-around;align-items:center;padding:0 14px}

/* support */
.support__label{left:20px;top:71px;font-size:8.5px;color:var(--ink-soft)}
.support__mic{left:168px;top:67px}
.support__field{left:20px;top:88px;width:157px;height:89px;background:var(--white);border-radius:2px}
.support__hint{left:8px;top:9px;font-size:6px;color:var(--muted)}

/* question */
.q__heading{left:20px;top:32px;font-size:10px;line-height:1.3;color:var(--ink-soft)}
.q__section{left:20px;top:65px;font-size:8.5px;color:var(--ink-soft)}
.q__topic{left:20px;top:83px;font-size:8.5px;line-height:1.55;color:var(--ink-soft)}
.q__ring-label{left:144px;width:40px;text-align:center;font-size:5.5px;line-height:1.3;color:var(--ink-soft)}
.q__number{left:20px;top:173px;font-size:10px;color:var(--ink-soft)}
.q__text{left:20px;top:187px;font-size:9px;line-height:1.45;color:var(--ink)}
.q__answer{left:20px;top:250px;width:157px;height:38px;background:var(--white);border-radius:2px;padding:7px 8px;font-size:8px;color:var(--ink-soft)}
.q__photo{left:42px;top:298px;width:113px;height:60px;border-radius:2px;
  background:linear-gradient(180deg,#D4D7DC,#B9BEC6)}
.btn--save{left:20px;top:370px;width:75px;height:21px;font-size:9px;color:var(--ink);background:linear-gradient(180deg,var(--gold),var(--gold-deep))}
.btn--next{left:101px;top:370px;width:76px;height:21px;font-size:9px;color:var(--white);background:var(--maroon)}
</style>
</head>
<body>

<!-- Welcome -->
<section class="screen screen--welcome">
  <p class="abs center-text welcome__headline">The most 'user-friendly' Fire Risk<br>Assessment App available.</p>
  <div class="abs welcome__preview" role="img" aria-label="Fanned stack of assessment question cards over soft flames"></div>
  <p class="abs center-text welcome__tagline">Quick tap responses and<br>voice-activated typing.</p>
  <svg class="abs" style="left:94px;top:231px" width="11" height="15" viewBox="0 0 11 15"><rect x="3" y="0.5" width="5" height="9" rx="2.5" fill="#8A8A8A"/><path d="M1 7a4.5 4.5 0 0 0 9 0M5.5 11.5V14M3 14h5" stroke="#8A8A8A" stroke-width="1" fill="none"/></svg>
  <div class="btn btn--create">
    <svg width="11" height="12" viewBox="0 0 11 12"><circle cx="5.5" cy="3.5" r="2.7" stroke="#333" fill="none"/><path d="M1 11.5c0-3 2-4.5 4.5-4.5s4.5 1.5 4.5 4.5z" stroke="#333" fill="none"/></svg>
    <span>Create a Free account</span>
  </div>
  <p class="abs center-text t welcome__note">Any Responsible Person can do it.</p>
  <div class="btn btn--login">
    <svg width="12" height="12" viewBox="0 0 12 12"><circle cx="6" cy="6" r="5.2" stroke="#fff" fill="none"/><path d="M3 6h5M6 3.8 8.2 6 6 8.2" stroke="#fff" fill="none"/></svg>
    <span>Customer Log in</span>
  </div>
  <div class="abs welcome__finger">
    <svg width="18" height="22" viewBox="0 0 18 22" fill="none" stroke="#8A8A8A" stroke-width="1"><path d="M2 8a7 7 0 0 1 14 0v6"/><path d="M4.5 17V8.5a4.5 4.5 0 0 1 9 0V16"/><path d="M7 19V9a2 2 0 0 1 4 0v9"/><path d="M9 10v11"/></svg>
  </div>
  <p class="abs center-text t welcome__footer">Created and endorsed by British Firefighters.</p>
</section>

<!-- Dashboard -->
<section class="screen screen--dashboard">
  <h1 class="abs center-text t screen__title" style="font-weight:400">
    <svg width="18" height="18" viewBox="0 0 18 18"><circle cx="9" cy="9" r="8" fill="#fff" stroke="#3A3A3A" stroke-width="1.4"/><path d="M3.5 11a5.5 5.5 0 0 1 11 0" stroke="#F0912C" stroke-width="2" fill="none"/><path d="M9 11 12 6" stroke="#EB3D1F" stroke-width="1.3"/></svg>
    <span>DASHBOARD</span>
  </h1>
  <p class="abs center-text t dash__start">Start Fire Risk Assessment</p>
  <svg class="abs" style="left:0;top:70px" width="199" height="92" viewBox="0 0 199 92">
    <path d="M88 33 66 56M110 33 132 56" stroke="#444" stroke-dasharray="1 2" fill="none"/>
    <circle cx="99" cy="20" r="16" fill="#EB1C24"/>
    <path d="M99 11v18M90 20h18" stroke="#fff" stroke-width="3"/>
    <circle cx="66" cy="72" r="16" fill="#fff"/>
    <circle cx="132" cy="72" r="16" fill="#fff"/>
  </svg>
  <div class="abs" style="left:58px;top:133px;width:16px;height:18px;border-radius:2px;background:linear-gradient(180deg,#D6E0EE,#8EA2C3)" role="img" aria-label="Commercial building"></div>
  <div class="abs" style="left:124px;top:133px;width:16px;height:18px;border-radius:2px;background:linear-gradient(180deg,#EC4F4E,#F7CA91)" role="img" aria-label="Residential house"></div>
  <p class="abs t dash__type" style="left:36px">Commercial</p>
  <p class="abs t dash__type" style="left:102px">Residential</p>

  <div class="status status--complete"><span>Complete</span>
    <svg width="10" height="10" viewBox="0 0 10 10"><circle cx="5" cy="5" r="5" fill="#fff"/><path d="M2.7 5.2 4.3 6.7 7.3 3.6" stroke="#1EC43C" stroke-width="1.3" fill="none"/></svg></div>
  <div class="site" style="top:219px"><i class="site__mark"></i>Rico's Barbershop</div>

  <div class="status status--progress"><span>In Progress</span>
    <svg width="10" height="10" viewBox="0 0 10 10"><circle cx="5" cy="5" r="3.8" stroke="#fff" stroke-width="1.6" fill="none" stroke-dasharray="18 6"/></svg></div>
  <div class="site" style="top:271px"><i class="site__mark"></i>Elm Rd School</div>
  <div class="site" style="top:289px"><i class="site__mark"></i>St Anne's Care Home</div>

  <div class="status status--purchases"><span>Purchases</span>
    <svg width="12" height="10" viewBox="0 0 12 10"><path d="M0.5 1h2l1.5 6h6l1.5-4.5H3.3" stroke="#fff" fill="none"/><circle cx="4.8" cy="9" r=".9" fill="#fff"/><circle cx="9" cy="9" r=".9" fill="#fff"/></svg></div>
  <div class="site site--small" style="top:343px"><i class="site__mark site__mark--home"></i>Residential Fire Risk Assessment</div>
  <div class="site site--small" style="top:361px"><i class="site__mark"></i>Commercial Fire Risk Assessment</div>
  <div class="site site--small" style="top:379px"><i class="site__mark"></i>Commercial Fire Risk Assessment</div>

  <nav class="nav">
    <svg width="14" height="14" viewBox="0 0 14 14"><circle cx="7" cy="7" r="6" fill="#fff" stroke="#3A3A3A" stroke-width="1.2"/><path d="M3 8.5a4 4 0 0 1 8 0" stroke="#F0912C" stroke-width="1.6" fill="none"/><path d="M7 8.5 9 5" stroke="#EB3D1F"/></svg>
    <svg width="15" height="11" viewBox="0 0 15 11"><rect x=".5" y=".5" width="14" height="10" rx="1.5" fill="var(--nav-icon)"/><rect x=".5" y="3" width="14" height="2" fill="#fff"/></svg>
    <svg width="14" height="13" viewBox="0 0 14 13"><path d="M1 1h12v8H5l-3 3V9H1z" fill="var(--nav-icon)"/><path d="M3.5 4h7M3.5 6h5" stroke="#fff"/></svg>
    <svg width="13" height="14" viewBox="0 0 13 14" fill="none" stroke="var(--nav-icon)" stroke-width="1.3"><path d="M2 1h6v12H2z"/><path d="M6 7h6M10 5l2 2-2 2"/></svg>
  </nav>
</section>

<!-- Technical support -->
<section class="screen screen--support">
  <h1 class="abs center-text t screen__title" style="font-weight:400">
    <svg width="15" height="14" viewBox="0 0 15 14"><path d="M1 1h13v9H5l-3 3v-3H1z" fill="var(--orange-icon)"/><path d="M3.5 4h8M3.5 6.5h5" stroke="#fff"/></svg>
    <span>TECHNICAL SUPPORT</span>
  </h1>
  <p class="abs t support__label">Type/record your response here</p>
  <svg class="abs support__mic" width="10" height="15" viewBox="0 0 10 15"><rect x="2.5" y=".5" width="5" height="9" rx="2.5" fill="#8A8A8A"/><path d="M.8 7a4.2 4.2 0 0 0 8.4 0M5 11.3V14M2.8 14h4.4" stroke="#8A8A8A" fill="none"/></svg>
  <div class="abs support__field"><p class="abs t support__hint">Type here</p></div>
  <nav class="nav">
    <svg width="14" height="14" viewBox="0 0 14 14"><circle cx="7" cy="7" r="6" fill="#fff" stroke="#6E6E6E" stroke-width="1.2"/><path d="M7 8 9 5" stroke="#6E6E6E"/></svg>
    <svg width="15" height="11" viewBox="0 0 15 11"><rect x=".5" y=".5" width="14" height="10" rx="1.5" fill="var(--nav-icon)"/><rect x=".5" y="3" width="14" height="2" fill="#fff"/></svg>
    <svg width="14" height="13" viewBox="0 0 14 13"><path d="M1 1h12v8H5l-3 3V9H1z" fill="var(--orange-icon)"/><path d="M3.5 4h7M3.5 6h5" stroke="#fff"/></svg>
    <svg width="13" height="14" viewBox="0 0 13 14" fill="none" stroke="var(--nav-icon)" stroke-width="1.3"><path d="M2 1h6v12H2z"/><path d="M6 7h6M10 5l2 2-2 2"/></svg>
  </nav>
</section>

<!-- Question -->
<section class="screen screen--question">
  <p class="abs t q__heading">Fire Risk ASSESSMENT<br>FIRE HAZARDS</p>
  <p class="abs t q__section">SECTION 7.00/30.00</p>
  <p class="abs t q__topic">ELECTRONIC SOURCES<br>OF IGNITION<br>(Clause 13 &amp; Annex B)</p>
  <svg class="abs" style="left:151px;top:34px" width="26" height="26" viewBox="0 0 26 26"><circle cx="13" cy="13" r="10.5" fill="none" stroke="var(--ring)" stroke-width="3.2" stroke-dasharray="58 8" transform="rotate(-60 13 13)"/></svg>
  <p class="abs q__ring-label" style="top:64px">Section<br>Progress</p>
  <svg class="abs" style="left:151px;top:89px" width="26" height="26" viewBox="0 0 26 26"><circle cx="13" cy="13" r="10.5" fill="none" stroke="var(--ring)" stroke-width="3.2" stroke-dasharray="56 10" transform="rotate(-40 13 13)"/></svg>
  <p class="abs q__ring-label" style="top:119px">Assesment<br>Progress</p>
  <svg class="abs" style="left:87px;top:138px" width="23" height="24" viewBox="0 0 23 24"><circle cx="11.5" cy="12" r="10.5" fill="none" stroke="#222" stroke-width="1.5"/><path d="M13 2 6 13h5l-2 9 8-12h-5z" fill="#FFC000"/></svg>
  <p class="abs t q__number">Q:7.01</p>
  <p class="abs q__text">Are reasonable measures taken to<br>prevent fires of electrical origin?</p>
  <svg class="abs" style="left:30px;top:219px" width="140" height="18" viewBox="0 0 140 18">
    <circle cx="8" cy="9" r="6.8" fill="none" stroke="#2BC93B" stroke-width="1.2"/><path d="M4.8 9.2 7.2 11.5 11.3 6.8" stroke="#2BC93B" stroke-width="1.2" fill="none"/>
    <circle cx="37" cy="9" r="6.8" fill="none" stroke="#EB1C24" stroke-width="1.2"/><path d="M34.3 6.3 39.7 11.7M39.7 6.3 34.3 11.7" stroke="#EB1C24" stroke-width="1.2"/>
    <circle cx="67" cy="9" r="6.8" fill="none" stroke="#F0912C" stroke-width="1.2"/><path d="M63.8 9h6.4" stroke="#F0912C" stroke-width="1.2"/>
    <rect x="92.5" y="1" width="5" height="10" rx="2.5" fill="#2E2E2E"/><path d="M91 9a4 4 0 0 0 8 0M95 13v4" stroke="#2E2E2E" fill="none"/>
    <path d="M118 5h3l1.5-2h5l1.5 2h3a1 1 0 0 1 1 1v8a1 1 0 0 1-1 1h-14a1 1 0 0 1-1-1V6a1 1 0 0 1 1-1z" fill="#2E2E2E"/><circle cx="125" cy="10" r="3" fill="#fff"/><circle cx="125" cy="10" r="1.6" fill="#2E2E2E"/>
  </svg>
  <div class="abs q__answer">No, electric sockets are overloaded</div>
  <div class="abs q__photo" role="img" aria-label="Photo of an overloaded multi-socket wall adaptor"></div>
  <div class="btn btn--save">Save + Close</div>
  <div class="btn btn--next">Next »</div>
  <nav class="nav">
    <svg width="14" height="14" viewBox="0 0 14 14"><circle cx="7" cy="7" r="6" fill="#fff" stroke="#3A3A3A" stroke-width="1.2"/><path d="M3 8.5a4 4 0 0 1 8 0" stroke="#F0912C" stroke-width="1.6" fill="none"/><path d="M7 8.5 9 5" stroke="#EB3D1F"/></svg>
    <svg width="15" height="11" viewBox="0 0 15 11"><rect x=".5" y=".5" width="14" height="10" rx="1.5" fill="var(--nav-icon)"/><rect x=".5" y="3" width="14" height="2" fill="#fff"/></svg>
    <svg width="14" height="13" viewBox="0 0 14 13"><path d="M1 1h12v8H5l-3 3V9H1z" fill="var(--nav-icon)"/><path d="M3.5 4h7M3.5 6h5" stroke="#fff"/></svg>
    <svg width="13" height="14" viewBox="0 0 13 14" fill="none" stroke="var(--nav-icon)" stroke-width="1.3"><path d="M2 1h6v12H2z"/><path d="M6 7h6M10 5l2 2-2 2"/></svg>
  </nav>
</section>

</body>
</html>
```